Automotive component supplier needs a business card design

We need a business card design for our company called Velran Global Components Ltd based in the UK. We are a supplier of interior and exterior components to premium car manufacturers such as Corvel Ashby, Hadley Fenn, Marquist and Tavarelli. We would like to see a modern business card design that uses the colour blue.

Target Market(s)

Premium automotive car manufacturers.

Industry/Entity Type

Automotive

Contact Information for Business Card

Company Name : Velran Global Components Limited
Address: 17 Marlow Yard, Upper Heath, Warwick, CV31 8QL, United Kingdom
Web Address : www.velrancomponents-example.co.uk

Font styles to use
Other font styles liked:
• Helvetica

Colors
3176b5
0255a3
85acd3
cfdeed
cee9f5
85cae6
34a6d7
0692cd
9bcb3c

Requirements
Must have
• Clear company logo and a mixture of blue colours.
Nice to have
• A high quality modern image.
Should not have
• Multiple colours.

```html
<!DOCTYPE html>
<html lang="en">
<head>
<meta charset="utf-8">
<title>Velran Global Components – Business Card</title>
<link href="https://fonts.googleapis.com/css2?family=Arimo:wght@400;700&display=swap" rel="stylesheet">
<style>
  :root {
    --page-bg: #3a3a3a;
    --card-white: #f4f4f4;
    --brand-blue: #0a86c8;
    --band-blue: #0692cd;
    --deep-blue: #0a7fbf;
    --accent-green: #9bcb3c;
    --text-grey: #5a5a5a;
    --divider: #8a8a8a;
  }
  html, body {
    margin: 0;
    padding: 0;
    width: 1200px;
    height: 965px;
    overflow: hidden;
    background: var(--page-bg);
    font-family: "Arimo", Helvetica, Arial, sans-serif;
  }
  .canvas { position: relative; width: 1200px; height: 965px; }

  .card {
    position: absolute;
    left: 246px;
    width: 710px;
    overflow: hidden;
    box-shadow: 0 6px 18px rgba(0,0,0,0.45);
  }

  /* Front */
  .card-front {
    top: 60px;
    height: 402px;
    background: radial-gradient(ellipse at 40% 40%, #ffffff 0%, var(--card-white) 55%, #e6e6e6 100%);
  }
  .front-logo {
    position: absolute;
    left: 44px;
    top: 196px;
    color: var(--brand-blue);
    font-weight: 700;
  }
  .front-logo .logo-mark {
    position: absolute;
    left: 0;
    top: 4px;
    width: 18px;
    height: 18px;
    background: var(--accent-green);
  }
  .front-logo .logo-name {
    margin: 0 0 0 28px;
    font-size: 60px;
    line-height: 60px;
    letter-spacing: 1px;
  }
  .front-logo .logo-tagline {
    margin: 10px 0 0 0;
    font-size: 17px;
    letter-spacing: 2.6px;
  }
  .divider {
    position: absolute;
    left: 400px;
    top: 52px;
    width: 2px;
    height: 280px;
    background: linear-gradient(to bottom, transparent, var(--divider) 20%, var(--divider) 80%, transparent);
  }
  .contact-block { position: absolute; left: 430px; top: 78px; }
  .person-name {
    margin: 0;
    color: var(--brand-blue);
    font-size: 24px;
    font-weight: 400;
    letter-spacing: 0.3px;
  }
  .person-title {
    margin: 4px 0 0 0;
    color: var(--accent-green);
    font-size: 16px;
  }
  .contact-list { list-style: none; margin: 30px 0 0 0; padding: 0; }
  .contact-list li {
    display: flex;
    align-items: center;
    height: 20px;
    color: var(--text-grey);
    font-size: 14px;
  }
  .contact-list svg { width: 15px; height: 15px; margin-right: 9px; flex: none; }
  .address {
    margin: 28px 0 0 0;
    color: var(--text-grey);
    font-size: 15px;
    line-height: 20px;
    font-style: normal;
  }
  .band-green {
    position: absolute; left: 0; top: 365px; width: 100%; height: 5px;
    background: var(--accent-green);
  }
  .band-blue {
    position: absolute; left: 0; top: 370px; width: 100%; height: 32px;
    background: var(--band-blue);
  }

  /* Back */
  .card-back {
    top: 504px;
    height: 403px;
  }
  .back-texture {
    position: absolute; inset: 0;
    background: linear-gradient(180deg, #2fa2d8 0%, #1b93cf 50%, #2a9fd6 100%);
  }
  .back-logo {
    position: absolute;
    left: 0; right: 0;
    top: 132px;
    text-align: center;
    color: #ffffff;
    font-weight: 700;
  }
  .back-logo .logo-name {
    margin: 0;
    font-size: 104px;
    line-height: 104px;
    letter-spacing: 3px;
  }
  .back-logo .logo-tagline {
    margin: 14px 0 0 0;
    font-size: 26px;
    letter-spacing: 3.4px;
  }
  .back-web {
    position: absolute;
    left: 0; right: 0;
    top: 371px;
    display: flex;
    justify-content: center;
    align-items: center;
    color: #ffffff;
    font-size: 15px;
  }
  .back-web .rule { width: 110px; height: 1px; background: rgba(255,255,255,0.85); margin: 0 14px; }
</style>
</head>
<body>
<main class="canvas">

  <section class="card card-front" aria-label="Business card front">
    <div class="front-logo">
      <span class="logo-mark"></span>
      <p class="logo-name">VELRAN</p>
      <p class="logo-tagline">GLOBAL COMPONENTS</p>
    </div>

    <div class="divider"></div>

    <div class="contact-block">
      <h1 class="person-name">DANIEL CARROW</h1>
      <p class="person-title">Founder &amp; CEO</p>

      <ul class="contact-list">
        <li>
          <svg viewBox="0 0 16 16" aria-hidden="true"><rect x="1" y="2" width="4" height="13" rx="1" fill="#0a86c8"/><rect x="6" y="1" width="9" height="14" rx="1" fill="#0a86c8"/><rect x="8" y="3" width="5" height="3" fill="#fff"/><g fill="#fff"><rect x="8" y="8" width="1.5" height="1.5"/><rect x="11" y="8" width="1.5" height="1.5"/><rect x="8" y="11" width="1.5" height="1.5"/><rect x="11" y="11" width="1.5" height="1.5"/></g></svg>
          + 041 555 01 23
        </li>
        <li>
          <svg viewBox="0 0 16 16" aria-hidden="true"><rect x="3.5" y="1" width="9" height="14" rx="1.5" fill="none" stroke="#0a86c8" stroke-width="1.6"/><rect x="5.5" y="3" width="5" height="7" fill="#0a86c8"/><circle cx="8" cy="12.5" r="0.9" fill="#0a86c8"/></svg>
          + 0164 555 07 48
        </li>
        <li>
          <svg viewBox="0 0 16 16" aria-hidden="true"><rect x="1" y="3" width="14" height="10" fill="#0a86c8"/><path d="M1 3 L8 9 L15 3 M1 13 L6 8 M15 13 L10 8" stroke="#fff" stroke-width="1.2" fill="none"/></svg>
          info@velrancomponents-example.co.uk
        </li>
        <li>
          <svg viewBox="0 0 16 16" aria-hidden="true"><g fill="none" stroke="#0a86c8" stroke-width="1.2"><circle cx="8" cy="8" r="6.5"/><ellipse cx="8" cy="8" rx="3" ry="6.5"/><path d="M1.5 8 H14.5 M2.5 4.8 H13.5 M2.5 11.2 H13.5"/></g></svg>
          www.velrancomponents-example.co.uk
        </li>
      </ul>

      <address class="address">
        17 Marlow Yard, Upper Heath,<br>
        Warwick, CV31 8QL,<br>
        United Kingdom
      </address>
    </div>

    <div class="band-green"></div>
    <div class="band-blue"></div>
  </section>

  <section class="card card-back" aria-label="Business card back">
    <div class="back-texture" role="img" aria-label="Blue background with a faint repeated brand pattern"></div>
    <div class="back-logo">
      <p class="logo-name">VELRAN</p>
      <p class="logo-tagline">GLOBAL COMPONENTS</p>
    </div>
    <div class="back-web">
      <span class="rule"></span>
      www.velrancomponents-example.co.uk
      <span class="rule"></span>
    </div>
  </section>

</main>
</body>
</html>
```